Design website for new email startup

We are starting a company called Pingo.QZ (it will live at http://pingo.qz).

We would like the main landing page for our site designed. We have provided a very simple wireframe to help provide direction for the content it should include, but we do not expect the designers to adhere to it at all - we encourage unique ideas. There is some sample text in the wireframe - this does not have to be used, but may provide ideas.

We provide an easy way for people to manage email for a custom domain name. For example if you own "yourhouseword.example" you can point your DNS records to us and we'll make it easy to have emails addressed to your domain get forwarded to your existing email (gmail, etc). Folks running blogs, and other small sites can quickly setup email addresses for their domains and manage them in one place.

(For technical folks, we have you point your dns mx records to us, hence the name. That way all your email hits us and we can redirect it wherever you want. We make it easy to manage a single domain or a bunch of domains. Many domain registrars offer this service for a fee, and have clumsy management tools. We provide a robust simple toolset for free, as well as premium options).

The goal of the landing page is to get folks into the signup flow. The second priority flow is to have them take a look at the premium plan offerings.

We may offer the winning designer additional work for the remainder of the site design.
Updates

I've changed this project to a committed payment.  It is no longer refundable.  Thank you.

Target Market(s)

Bloggers, podcasters, designers, app developers - people who are a little tech savvy.

Industry/Entity Type

It Company

Font styles to use
Sans Serif

Colors

Designer to choose colors to be used in the design.

Requirements
Must have
• A full fidelity mockup (comp) of the landing page including the source file (psd, ai, etc).

Some sort of logo treatment for the pingo.qz brand

A call to action for signup, such as the suggested 'Get Started Here'
Nice to have
• A hip startup feel

Incorporation of the email theme

Give the impression it is simple, easy and fast

```html
<!DOCTYPE html>
<html lang="en">
<head>
<meta charset="utf-8">
<title>Pingo.QZ — Email for your domain</title>
<link rel="stylesheet" href="https://fonts.googleapis.com/css2?family=Exo+2:wght@400;700&family=Open+Sans:wght@400;600;700&display=swap">
<style>
  :root{
    --brand-blue:#1e7fc6;
    --ink:#2b2b2b;
    --muted:#8a8a8a;
    --link-blue:#2f86c0;
    --hero-dark:#0c2f33;
    --hero-mid:#185a60;
    --hero-light:#2d8a8e;
    --btn-blue-top:#6fb2ea;
    --btn-blue-bottom:#3a86cf;
    --btn-grey-top:#f4f4f4;
    --btn-grey-bottom:#cfcfcf;
    --tick:#6fc23a;
    --card-border:#cfcfcf;
    --footer-top:#f7f8f9;
    --footer-bottom:#e4e6e8;
    --social:#6d6f72;
  }
  *{box-sizing:border-box;margin:0;padding:0}
  html,body{width:1200px;height:656px;overflow:hidden;background:#fff;font-family:"Open Sans",Arial,sans-serif;color:var(--ink)}
  .page{position:relative;width:1200px;height:656px}

  .site-header{position:absolute;left:0;top:0;width:1200px;height:73px;background:linear-gradient(#fff,#f1f3f5);border-bottom:2px solid #4a4f54}
  .logo{position:absolute;left:112px;top:20px;font-family:"Exo 2",sans-serif;font-weight:700;font-size:28px;color:var(--brand-blue);letter-spacing:.5px}
  .utility-nav{position:absolute;right:110px;top:11px;display:flex;gap:20px;font-size:13px}
  .utility-nav a{display:flex;align-items:center;gap:5px;color:var(--ink);text-decoration:none}
  .main-nav{position:absolute;right:111px;top:45px;font-size:14px;display:flex;gap:15px}
  .main-nav a{color:var(--ink);text-decoration:none}

  .hero{position:absolute;left:0;top:73px;width:1200px;height:350px;background:radial-gradient(ellipse at 78% 40%,var(--hero-light),var(--hero-mid) 45%,var(--hero-dark) 85%)}
  .hero-art{position:absolute;left:620px;top:0;width:580px;height:350px;background:radial-gradient(circle at 55% 45%,rgba(150,220,220,.35),rgba(40,120,125,.15) 60%,transparent 80%)}
  .hero-title{position:absolute;left:110px;top:40px;font-family:"Exo 2",sans-serif;font-weight:400;font-size:38px;color:#fff;letter-spacing:.5px}
  .features{position:absolute;left:108px;top:99px;list-style:none;color:#fff;font-size:11.6px;white-space:nowrap}
  .features li{display:flex;align-items:center;gap:10px;height:26px}
  .features .note{padding-left:29px;height:auto;margin-top:2px;line-height:16px;display:block;font-family:Arial,Helvetica,sans-serif;font-size:12.5px}
  .btn{position:absolute;top:263px;height:54px;border-radius:6px;font-family:"Open Sans",sans-serif;font-weight:700;font-size:18px;display:flex;align-items:center;justify-content:center;letter-spacing:-.5px;text-decoration:none}
  .btn-primary{left:103px;width:198px;background:linear-gradient(var(--btn-blue-top),var(--btn-blue-bottom));color:#fff;box-shadow:0 2px 3px rgba(0,0,0,.3)}
  .btn-secondary{left:322px;width:198px;background:linear-gradient(var(--btn-grey-top),var(--btn-grey-bottom));color:#222;box-shadow:0 2px 3px rgba(0,0,0,.3)}
  .slider-control{position:absolute;left:570px;top:297px;width:48px;height:48px;border-radius:50%;background:#0b1416}

  .guide-card{position:absolute;border:1px solid var(--card-border);border-radius:8px;background:#fff}
  .guide-card.first{left:99px;top:432px;width:489px;height:141px}
  .guide-card.second{left:597px;top:434px;width:505px;height:141px}
  .guide-art{position:absolute}
  .first .guide-art{left:6px;top:16px;width:106px;height:106px;border-radius:50%;background:radial-gradient(circle at 40% 35%,#d9d9d9,#555 55%,#1a1a1a)}
  .second .guide-art{left:15px;top:20px;width:124px;height:94px;background:linear-gradient(90deg,#3a3a3a,#c9c9c9 40%,#5a5a5a 70%,#b5b5b5)}
  .guide-title{position:absolute;font-family:"Exo 2",sans-serif;font-weight:400;font-size:14px;line-height:22px;color:var(--link-blue);text-transform:uppercase;white-space:nowrap}
  .first .guide-title{left:131px;top:16px}
  .second .guide-title{left:152px;top:15px}
  .guide-text{position:absolute;font-size:12px;line-height:18px;color:var(--muted);text-align:justify}
  .first .guide-text{left:128px;top:71px;width:341px}
  .second .guide-text{left:151px;top:70px;width:341px}

  .site-footer{position:absolute;left:0;top:578px;width:1200px;height:78px;background:linear-gradient(var(--footer-top),var(--footer-bottom));border-top:1px solid #ddd}
  .footer-nav{position:absolute;left:103px;top:24px;font-size:12.5px;display:flex;gap:12px}
  .footer-nav a{color:var(--ink);text-decoration:none}
  .social{position:absolute;left:538px;top:28px;display:flex;gap:8px}
  .social span{width:20px;height:20px;border-radius:50%;background:var(--social)}
  .legal{position:absolute;right:104px;top:27px;font-family:Arial,Helvetica,sans-serif;font-size:13px;color:var(--ink)}
</style>
</head>
<body>
<div class="page">
  <header class="site-header">
    <div class="logo">PINGO.QZ</div>
    <nav class="utility-nav">
      <a href="#"><svg width="14" height="14" viewBox="0 0 14 14"><circle cx="5.5" cy="5.5" r="4" fill="none" stroke="#2a6fc0" stroke-width="2"/><line x1="8.5" y1="8.5" x2="13" y2="13" stroke="#2a6fc0" stroke-width="2.5"/></svg>Search</a>
      <a href="#"><svg width="13" height="14" viewBox="0 0 13 14"><circle cx="6.5" cy="4" r="3.5" fill="#2a6fc0"/><path d="M0 14c0-5 13-5 13 0z" fill="#2a6fc0"/></svg>Support</a>
      <a href="#"><svg width="18" height="14" viewBox="0 0 18 14"><rect x="0" y="0" width="12" height="8" rx="2" fill="#2a6fc0"/><rect x="5" y="4" width="12" height="8" rx="2" fill="#4a8fd8"/></svg>Live Chat</a>
    </nav>
    <nav class="main-nav">
      <a href="#">HOW IT WORKS</a><span>|</span><a href="#">SUPPORTY</a><span>|</span><a href="#">LOGIN</a>
    </nav>
  </header>

  <section class="hero">
    <div class="hero-art" role="img" aria-label="World map with glowing email bubbles linked to a smartphone held in a hand"></div>
    <h1 class="hero-title">WEB HOSTING</h1>
    <ul class="features">
      <li><svg width="19" height="15" viewBox="0 0 19 15"><path d="M1 8l6 6L18 2" fill="none" stroke="var(--tick)" stroke-width="4"/></svg>WE MAKE EMAOL EASY.</li>
      <li><svg width="19" height="15" viewBox="0 0 19 15"><path d="M1 8l6 6L18 2" fill="none" stroke="var(--tick)" stroke-width="4"/></svg>GIVE US FIVE MINUTES AND WE'LL GET YOU EMAIL FROM YOUR DOMAIN.</li>
      <li><svg width="19" height="15" viewBox="0 0 19 15"><path d="M1 8l6 6L18 2" fill="none" stroke="var(--tick)" stroke-width="4"/></svg>EASILY FORWARD MAIL FROM YOUR &nbsp;CUSTOM DOMAIN NAME WHEREEVER YOU WANT IT.</li>
      <li><svg width="19" height="15" viewBox="0 0 19 15"><path d="M1 8l6 6L18 2" fill="none" stroke="var(--tick)" stroke-width="4"/></svg>YOU TAKE THE MAIL WE'LL KEEP THE SPAM.</li>
      <li class="note">SOMEWHERE WE NEED A LINK TO PLAN / PRINCING OPTIONS, ALTHOUGH THE<br>FREE TIER IS ENCOURAGED FOR INITIAL SIGNUP</li>
    </ul>
    <a class="btn btn-primary" href="#">GET STARTED FREE</a>
    <a class="btn btn-secondary" href="#">COMPARE PLANS</a>
    <div class="slider-control">
      <svg width="48" height="48" viewBox="0 0 48 48"><path d="M20 17l-6 7 6 7M28 17l6 7-6 7" fill="none" stroke="#fff" stroke-width="2"/></svg>
    </div>
  </section>

  <article class="guide-card first">
    <div class="guide-art" role="img" aria-label="Glossy dark globe with light trails"></div>
    <h2 class="guide-title">How to configure your Skyveil<br>DNS to use Pingo.QZ</h2>
    <p class="guide-text">How to configure your Skyveil DNS to use pingo.qz pingo.qz with your NameHarbor domain registration for reliable email forwarding</p>
  </article>

  <article class="guide-card second">
    <div class="guide-art" role="img" aria-label="Row of silver server towers"></div>
    <h2 class="guide-title">Use Pingo.QZ with your NameHarbor domain<br>&nbsp;registration for reliable email forwarding</h2>
    <p class="guide-text">How to configure your Skyveil DNS to use pingo.qz pingo.qz with your NameHarbor domain registration for reliable email forwarding</p>
  </article>

  <footer class="site-footer">
    <nav class="footer-nav"><a href="#">How it works</a><span>|</span><a href="#">Supporty</a><span>|</span><a href="#">Login</a></nav>
    <div class="social"><span></span><span></span><span></span><span></span></div>
    <div class="legal">PINGO.QZ © 2014 &nbsp;| &nbsp;PRIVACY POLICY</div>
  </footer>
</div>
</body>
</html>
```